Im open to ideas.. I was thinking on my business cards aswell as my logo. a place for my name. email. phone number and abn..

ive attched a file with my business logo. which i dont love the colours.. i was think a dark background with charcoal letters so something along those colour schumes but im open to ideas..

BRM Constructions

```html
<!DOCTYPE html>
<html lang="en">
<head>
<meta charset="utf-8">
<title>BRM Constructions – Business Card</title>
<link rel="stylesheet" href="https://fonts.googleapis.com/css2?family=Exo+2:wght@400;600;700;800&display=swap">
<style>
  :root {
    --backdrop: #1f1f1f;
    --card: #f4f4f4;
    --card-edge: #e6e6e6;
    --ink: #1b1b1b;
    --ink-soft: #3a3a3a;
    --brand-red: #c0181f;
    --on-red: #ffffff;
  }
  * { box-sizing: border-box; margin: 0; padding: 0; }
  html, body {
    width: 1200px; height: 873px; overflow: hidden;
    background: var(--backdrop);
    font-family: "Exo 2", sans-serif;
  }
  .stage {
    width: 1200px; height: 873px;
    display: flex; align-items: center; justify-content: center;
  }
  .business-card {
    position: relative;
    width: 840px; height: 480px;
    background: linear-gradient(160deg, #ffffff 0%, var(--card) 55%, var(--card-edge) 100%);
    overflow: hidden;
  }
  .brand {
    position: absolute; left: 150px; top: 84px;
    display: flex; align-items: center; gap: 12px;
  }
  .brand-mark {
    width: 22px; height: 22px; background: var(--brand-red);
  }
  .brand-name {
    font-weight: 800; font-size: 40px; letter-spacing: 1px;
    color: var(--ink); text-transform: uppercase; line-height: 1;
  }
  .person {
    position: absolute; right: 110px; top: 168px; text-align: right;
  }
  .person-name {
    font-weight: 700; font-size: 24px; color: var(--brand-red);
  }
  .person-role {
    font-size: 14px; color: var(--ink-soft); margin-top: 2px;
  }
  .contact {
    position: absolute; left: 44px; top: 246px;
    color: var(--ink-soft); font-size: 17px;
  }
  .contact-line {
    display: flex; align-items: center; gap: 10px; margin-bottom: 10px;
  }
  .contact-icon { width: 16px; height: 16px; flex: none; }
  .address {
    font-weight: 700; font-size: 20px; color: var(--ink); line-height: 1.3;
    margin-top: 4px;
  }
  .skyline-band {
    position: absolute; left: 0; right: 0; bottom: 0; height: 110px;
    background: var(--brand-red);
  }
  .website {
    position: absolute; left: 0; right: 0; bottom: 28px;
    text-align: center; color: var(--on-red);
    font-weight: 700; font-size: 22px; letter-spacing: 3px;
  }
</style>
</head>
<body>
<main class="stage">
  <article class="business-card">
    <div class="brand">
      <span class="brand-mark"></span>
      <span class="brand-name">BRM Constructions</span>
    </div>

    <div class="person">
      <p class="person-name">Daniel Harlow</p>
      <p class="person-role">Owner / Founder</p>
    </div>

    <div class="contact">
      <p class="contact-line">
        <svg class="contact-icon" viewBox="0 0 16 16" aria-hidden="true">
          <path fill="#c0181f" d="M3 2h3l1 3-2 1.2a8 8 0 0 0 4.8 4.8L11 9l3 1v3a1 1 0 0 1-1 1A12 12 0 0 1 2 3a1 1 0 0 1 1-1z"/>
        </svg>
        <span>0400555018</span>
      </p>
      <p class="contact-line">
        <svg class="contact-icon" viewBox="0 0 16 16" aria-hidden="true">
          <rect x="1" y="3" width="14" height="10" fill="#c0181f"/>
          <path d="M1 3l7 5 7-5" fill="none" stroke="#ffffff" stroke-width="1.3"/>
        </svg>
        <span>info@brmconstructions.com</span>
      </p>
      <p class="address">48 harbour lane<br>Seaview park ny 10990</p>
    </div>

    <div class="skyline-band" role="img" aria-label="Red city skyline silhouette along the bottom of the card"></div>
    <p class="website">www.brmconstructions.com</p>
  </article>
</main>
</body>
</html>
```